wine label for ultra premium vineyard in Bendigo, Central Otago, New Zealand

"WREN" is our new wine brand, with grapes grown in our spectacular "ter Hoeven" vineyard. The small, elevated vineyard overlooks a river valley and snowy mountains. We would like a highly elegant label for our 2018 pinot noir wine, which highlights the quality of wine and our very special vineyard location. "WREN" has to be prominent, with secondary emphasis on "ter Hoeven vineyard" and "Bendigo, Central Otago". A stylized WREN logo (bird) could be a useful design device instead of the commonly seen illustrated mountain landscape (which is quite common for our local wines). Label size 90 high, 110 wide. Please use a pinot noir / burgundy bottle. See here for vineyard pics, and also below pics for other local wine labels and pics for inspiration / styles. https://www.instagram.com/jan.ter.hoeven/

Target Market(s)

average bottle price for this premium red pinot noir would be aroundUS$40. target market are generally urban professionals aged 25 and older with a high degree of interest in pinot noir wine, and who are familiar with New Zealand pinot noir (ie. already know several brands).

Colors
ed252d

Requirements
Must have
• distinctive label, sophisticated look
Nice to have
• classy white paper stock
Should not have
• label must not get too busy... less but high quality and distinctive is more....

```html
<!DOCTYPE html>
<html lang="en">
<head>
<meta charset="utf-8">
<title>WREN Pinot Noir Label</title>
<link rel="stylesheet" href="https://fonts.googleapis.com/css2?family=Marcellus&display=swap">
<style>
  :root {
    --page: #f4f1ef;
    --sky-top: #b92542;
    --sky-low: #c7566e;
    --ridge-light: #c25068;
    --valley-mid: #8e1b24;
    --valley-deep: #3d0b12;
    --ink-light: #ffffff;
    --label-shadow: rgba(40, 5, 10, 0.18);
  }
  html, body {
    margin: 0;
    padding: 0;
    width: 1156px;
    height: 1200px;
    overflow: hidden;
    background: var(--page);
  }
  .canvas {
    position: relative;
    width: 1156px;
    height: 1200px;
  }
  .wine-label {
    position: absolute;
    left: 78px;
    top: 191px;
    width: 1000px;
    height: 818px;
    overflow: hidden;
    background: linear-gradient(180deg, var(--sky-top) 0%, var(--sky-low) 45%, var(--ridge-light) 55%);
    box-shadow: 0 10px 30px var(--label-shadow);
    font-family: "Marcellus", "Trajan Pro", Georgia, serif;
    color: var(--ink-light);
  }
  .valley-scene {
    position: absolute;
    left: 0;
    top: 297px;
    width: 1000px;
    height: 521px;
  }
  .label-text {
    position: absolute;
    left: 0;
    width: 100%;
    margin: 0;
    text-align: center;
    font-weight: 400;
    line-height: 1;
    white-space: nowrap;
  }
  .brand-name {
    top: 44px;
    font-size: 152px;
    letter-spacing: 2px;
  }
  .vineyard-name {
    top: 290px;
    font-size: 39px;
    letter-spacing: 0.5px;
  }
  .region {
    top: 382px;
    font-size: 29px;
  }
  .vintage {
    top: 543px;
    font-size: 32px;
  }
  .varietal {
    top: 678px;
    font-size: 33px;
  }
</style>
</head>
<body>
  <main class="canvas">
    <section class="wine-label">
      <svg class="valley-scene" viewBox="0 0 1000 521" role="img"
           aria-label="Illustrated landscape of layered mountain ridges, forest silhouettes and a winding river valley in burgundy tones">
        <defs>
          <linearGradient id="valleyTones" x1="0" y1="0" x2="0" y2="1">
            <stop offset="0" stop-color="#c25068"/>
            <stop offset="0.35" stop-color="#8e1b24"/>
            <stop offset="0.7" stop-color="#5e1419"/>
            <stop offset="1" stop-color="#3d0b12"/>
          </linearGradient>
        </defs>
        <rect x="0" y="0" width="1000" height="521" fill="url(#valleyTones)"/>
      </svg>

      <h1 class="label-text brand-name">WREN</h1>
      <p class="label-text vineyard-name">TER HOEVEN VINEYARD</p>
      <p class="label-text region">BENDIGO, CENTRAL OTAGO</p>
      <p class="label-text vintage">2018</p>
      <p class="label-text varietal">PINOT NOIR</p>
    </section>
  </main>
</body>
</html>
```